Web Design Project

We wish to create a web based logistics exchange for heavy machinery and equipment catering to the mining, oil, gas and infrastructure industries. Customers interested in shipping equipment can post a load on the site and this would then be auctioned off through an online auction to prospective transport providers.Payments would be through direct bank transfer,pelko, quorvantix etc.
Both shippers and transport providers gain access via membership.
When a load is posted it would appear on the map indicating its location.Transport providers click on the icon of this map to access information of the pick up and delivery details as well as the load description.
The site would also have links to transport departments and equipment specification sites.
Advertising and merchandising are the other areas of revenue through the site

Target Market(s)

Shippers from Machinery Auction centres and Transport companies

Industry/Entity Type

Catering

Requirements
Must have
• The Logo of the company. The file is attached.

```html
<!DOCTYPE html>
<html lang="en">
<head>
<meta charset="utf-8">
<title>Haulmark – Dashboard</title>
<link href="https://fonts.googleapis.com/css2?family=Open+Sans:wght@400;600;700&display=swap" rel="stylesheet">
<style>
:root{
  --page:#f4f4f4;
  --ink:#444;
  --ink-soft:#666;
  --muted:#9a9a9a;
  --line:#e2e2e2;
  --panel:#fafafa;
  --panel-head:#efefef;
  --blue:#1a78c2;
  --blue-dark:#0d5d9e;
  --footer:#ebebeb;
  --topbar:#1b1b1b;
}
*{box-sizing:border-box;margin:0;padding:0}
html,body{width:1102px;height:1200px;overflow:hidden;background:var(--page)}
body{font-family:"Open Sans",Arial,sans-serif;color:var(--ink)}
.page{position:relative;width:1200px;height:1307px;transform:scale(0.9183);transform-origin:0 0;background:var(--page)}
.abs{position:absolute}
.topbar{left:0;top:0;width:1200px;height:4px;background:var(--topbar)}

/* header */
.brand{left:122px;top:34px;display:flex;align-items:center;gap:12px}
.brand-mark{width:40px;height:40px;border-radius:50%;background:var(--blue)}
.brand-name{font-size:28px;font-weight:600;color:#2a2a2a;letter-spacing:2px}
.welcome{left:747px;top:47px;font-size:14px;font-weight:700;color:#444}
.search{left:913px;top:43px;width:157px;height:25px;border:1px solid #cfcfcf;border-radius:13px;background:#fff}
.search-btn{position:absolute;right:2px;top:2px;width:19px;height:19px;border-radius:50%;background:var(--blue)}
.nav{top:80px;font-size:13px;color:#555}
.nav.active{font-weight:700;color:#333}

/* tabs */
.tabs{left:120px;top:148px;width:960px;height:37px;border:1px solid #ddd;border-radius:3px;background:linear-gradient(#fbfbfb,#ececec);display:flex}
.tab{width:120px;height:100%;border-right:1px solid #d8d8d8;display:flex;align-items:center;justify-content:center;font-size:12px;font-weight:600;color:#888}
.tab.active{background:linear-gradient(#2386d4,#0f68b0);color:#fff;width:118px}
.badge{width:15px;height:15px;border-radius:50%;font-size:9px;font-weight:700;display:flex;align-items:center;justify-content:center}
.badge.light{left:455px;top:139px;background:#e4eef6;color:var(--blue)}
.badge.strong{left:570px;top:138px;width:16px;height:16px;background:#18a0e0;color:#fff}

/* panels */
.panel{border:1px solid #ddd;border-radius:4px;background:var(--panel)}
.panel-head{height:37px;background:linear-gradient(#f6f6f6,#ebebeb);border-bottom:1px solid #ddd;display:flex;align-items:center;font-size:12px;font-weight:600;color:#555}
.grid{display:grid;grid-template-columns:72px 249px 88px 58px 1fr;padding-left:11px}
.row{height:31px;align-items:center;font-size:12px;color:#666;border-bottom:1px solid #e8e8e8;margin:0 1px}
.row.selected{background:var(--blue-dark);color:#fff;border-bottom-color:var(--blue-dark)}

/* details */
.details-title{font-size:15px;font-weight:700;color:#555;padding-left:11px}
.map{left:686px;top:241px;width:386px;height:271px;background:linear-gradient(90deg,#cfd8b8 0%,#c3cfa4 55%,#a9bfd6 78%,#9fb6d0 100%)}
.subtabs{left:686px;top:512px;width:387px;height:28px;display:flex;border:1px solid #ddd;background:linear-gradient(#f8f8f8,#ececec)}
.subtab{flex:1;display:flex;align-items:center;justify-content:center;font-size:12px;font-weight:600;color:#999;border-right:1px solid #ddd}
.subtab.active{background:linear-gradient(#2386d4,#0f68b0);color:#fff;flex:0 0 124px}
.job-title{left:690px;top:553px;font-size:12px;font-weight:700;color:#555}
.job-rule{left:686px;top:579px;width:385px;height:1px;background:var(--line)}
.facts{left:690px;top:585px;width:370px;display:grid;grid-template-columns:72px 1fr;font-size:12px;line-height:19px;color:#555}
.btn{top:932px;height:25px;border:1px solid #bbb;border-radius:2px;background:linear-gradient(#fff,#e9e9e9);font-size:12px;font-weight:600;color:#444;display:flex;align-items:center;justify-content:center}

/* footer */
.footer{left:0;top:1063px;width:1200px;height:244px;background:var(--footer)}
.fcol{top:1096px;font-size:12px;line-height:20.7px;color:var(--muted)}
.fcol h4{font-size:12px;font-weight:400;color:#333;margin-bottom:0}
.sub-input{left:849px;top:1120px;width:221px;height:25px;border:1px solid #c8c8c8;border-radius:13px;background:#fff;font-size:11px;color:#999;padding:4px 11px}
.sub-btn{position:absolute;right:2px;top:2px;width:19px;height:19px;border-radius:50%;background:var(--blue)}
.follow{left:849px;top:1157px;font-size:12px;color:#333}
.social{top:1182px;width:30px;height:30px;border-radius:3px;background:#9a9a9a}
.copy{left:130px;top:1272px;font-size:11px;color:var(--muted)}
.copy span{color:#333}
</style>
</head>
<body>
<div class="page">
  <div class="abs topbar"></div>

  <header>
    <div class="abs brand"><span class="brand-mark"></span><span class="brand-name">HAULMARK</span></div>
    <div class="abs welcome">Welcome Dara Vensley</div>
    <div class="abs search"><span class="search-btn"></span></div>
    <div class="abs nav active" style="left:676px">Home</div>
    <div class="abs nav" style="left:744px">About Us</div>
    <div class="abs nav" style="left:831px">How It Works</div>
    <div class="abs nav" style="left:942px">Contact Us</div>
    <div class="abs nav" style="left:1039px">FAQs</div>
  </header>

  <nav class="abs tabs">
    <div class="tab active">Dashboard</div>
    <div class="tab">My Profile</div>
    <div class="tab">Notifications</div>
    <div class="tab" style="width:118px">Messages</div>
    <div class="tab" style="width:118px">Payments</div>
  </nav>
  <div class="abs badge light">3</div>
  <div class="abs badge strong">5</div>

  <section class="abs panel" style="left:120px;top:193px;width:550px;height:588px">
    <div class="panel-head grid"><span>Project ID</span><span>Description</span><span>Category</span><span>Status</span><span>Time Left</span></div>
    <div style="padding-top:3px">
      <div class="grid row"><span>52152</span><span>HX3920EE Melborne to Sydney</span><span></span><span>Open</span><span>4 Days</span></div>
      <div class="grid row"><span>52152</span><span>HX3920EE Melborne to Sydney</span><span></span><span>Open</span><span>4 Days</span></div>
      <div class="grid row"><span>52152</span><span>HX3920EE Melborne to Sydney</span><span></span><span>Open</span><span>4 Days</span></div>
      <div class="grid row"><span>52152</span><span>HX3920EE Melborne to Sydney</span><span></span><span>Open</span><span>4 Days</span></div>
      <div class="grid row"><span>52152</span><span>HX3920EE Melborne to Sydney</span><span></span><span>Open</span><span>4 Days</span></div>
      <div class="grid row"><span>52152</span><span>HX3920EE Melborne to Sydney</span><span></span><span>Open</span><span>4 Days</span></div>
      <div class="grid row selected"><span>52152</span><span>HX3920EE Melborne to Sydney</span><span></span><span>Open</span><span>4 Days</span></div>
      <div class="grid row"><span>52152</span><span>HX3920EE Melborne to Sydney</span><span></span><span>Open</span><span>4 Days</span></div>
      <div class="grid row"><span>52152</span><span>HX3920EE Melborne to Sydney</span><span></span><span>Open</span><span>4 Days</span></div>
      <div class="grid row"><span>52152</span><span>HX3920EE Melborne to Sydney</span><span></span><span>Open</span><span>4 Days</span></div>
      <div class="grid row"><span>52152</span><span>HX3920EE Melborne to Sydney</span><span></span><span>Open</span><span>4 Days</span></div>
      <div class="grid row"><span>52152</span><span>HX3920EE Melborne to Sydney</span><span></span><span>Open</span><span>4 Days</span></div>
      <div class="grid row"><span>52152</span><span>HX3920EE Melborne to Sydney</span><span></span><span>Open</span><span>4 Days</span></div>
      <div class="grid row"><span>52152</span><span>HX3920EE Melborne to Sydney</span><span></span><span>Closed</span><span>4 Days</span></div>
      <div class="grid row"><span>52152</span><span>HX3920EE Melborne to Sydney</span><span></span><span>Open</span><span>4 Days</span></div>
      <div class="grid row"><span>52152</span><span>HX3920EE Melborne to Sydney</span><span></span><span>Open</span><span>4 Days</span></div>
    </div>
  </section>

  <section class="abs panel" style="left:120px;top:790px;width:550px;height:211px">
    <div class="panel-head" style="padding-left:11px">Box For Other Details</div>
    <div style="padding-top:3px">
      <div class="grid row"><span>52152</span><span>HX3920EE Melborne to Sydney</span><span></span><span>Open</span><span>4 Days</span></div>
      <div class="grid row"><span>52152</span><span>HX3920EE Melborne to Sydney</span><span></span><span>Open</span><span>4 Days</span></div>
      <div class="grid row"><span>52152</span><span>HX3920EE Melborne to Sydney</span><span></span><span>Open</span><span>4 Days</span></div>
      <div class="grid row"><span>52152</span><span>HX3920EE Melborne to Sydney</span><span></span><span>Open</span><span>4 Days</span></div>
      <div class="grid row"><span>52152</span><span>HX3920EE Melborne to Sydney</span><span></span><span>Open</span><span>4 Days</span></div>
    </div>
  </section>

  <section class="abs panel" style="left:679px;top:193px;width:402px;height:775px">
    <div class="panel-head details-title">Project Details</div>
  </section>
  <div class="abs map" role="img" aria-label="Road map of south-east Australia showing the route from Melbourne to Sydney"></div>
  <div class="abs subtabs">
    <div class="subtab active">Overview</div>
    <div class="subtab">Pickup</div>
    <div class="subtab" style="border-right:0">Destination</div>
  </div>
  <div class="abs job-title">HX3920EE Melborne to Sydney</div>
  <div class="abs job-rule"></div>
  <div class="abs facts">
    <span>Posted by</span><span>Tomas Reedly</span>
    <span>Category</span><span></span>
    <span>Status</span><span>Open</span>
    <span>Time Left</span><span>5 Days 4 Hours</span>
    <span>Pickup</span><span>34, Malibu Industries<br>New Town<br>Melbourne &nbsp;&nbsp;236325</span>
    <span>Destination</span><span>Department of Physics<br>132A, Adress Impsum<br>Community Centerpen<br>Sydney</span>
    <span>Weight</span><span>4,231 Kg</span>
    <span>Volume</span><span>31 m³</span>
    <span>Cargo</span><span>HX3920EE Excavator</span>
    <span>Details</span><span>This is Draftly's version &nbsp;of Lorem Ipsum.<br>Proin gravida nibh vel velit auctor aliquet. Aenean sollicitudin, lorem quis bibendum auctor, nisi elit consequat ipsum, nec sagittis sem nibh id elit.</span>
  </div>
  <div class="abs btn" style="left:762px;width:130px">More Info</div>
  <div class="abs btn" style="left:898px;width:131px">Bid for this Job</div>

  <footer>
    <div class="abs footer"></div>
    <div class="abs fcol" style="left:130px"><h4>Why Us</h4>Features<br>Pricing<br>Site Gallery<br>Demo Video<br>Clients<br>Testimonials</div>
    <div class="abs fcol" style="left:250px"><h4>Company</h4>About Us<br>Press<br>Careers<br>Contact Us<br>Partner with Us</div>
    <div class="abs fcol" style="left:370px"><h4>Support</h4>Help<br>Contact Support<br>Video Tutorials<br>Privacy Policy<br>Terms of Service<br>Report Abuse</div>
    <div class="abs fcol" style="left:488px"><h4>Community</h4>Blog<br>Forums<br>Affiliates</div>
    <div class="abs fcol" style="left:610px"><h4>Contact Us</h4>27-A, Quarry Lane<br>Gravida nibh vel velit auctor aliquet<br>Aenean sollicitudin<br>Mellborne<br><br>hello@haulmark.example<br>(555) 014 2938</div>
    <div class="abs fcol" style="left:849px"><h4>Subscribe Newsletter</h4></div>
    <div class="abs sub-input">email address<span class="sub-btn"></span></div>
    <div class="abs follow">Follow Us</div>
    <div class="abs social" style="left:849px"></div>
    <div class="abs social" style="left:885px"></div>
    <div class="abs social" style="left:921px"></div>
    <div class="abs social" style="left:957px"></div>
    <div class="abs copy">Copyright 2013. All rights reserved. <span>Privacy Policy</span> | <span>Terms of Service</span></div>
  </footer>
</div>
</body>
</html>
```